indépendant en tant que Massothérapeute et Préparateur Mental, j'ai besoin de ...

Massothérapeute et préparateur mental indépendant, je recherche une carte de visite sobre et dynamique, sans images liées au massage ou à la préparation mentale mais intégrant mon logo. Les couleurs que j'aime bien sont : Blanc, gris, anthracite, noir et jaune

Contact Information for Business Card

carte de préférence Horizontale
neutre qui puisse toucher le deux domaines Massothérapie et préparation mentale

Requirements
Must have
• mon projet doit intégrer au recto:
LOGO
Loïc Bardèze
078 513 26 48
info@loicbardeze.ch
et éventuellement www.loicbardeze.ch

et au verso les deux adresses:

Chemin des Ormilles 7B
1400 Yverdon-les-Bains

Route de la Gravière 9
1700 Fribourg

Should not have
• mon projet ne doit pas contenir d'image en liens avec le massage ni la préparation mentale.

```html
<!DOCTYPE html>
<html lang="fr">
<head>
<meta charset="utf-8">
<title>Loïc Bardèze – Carte de visite</title>
<link href="https://fonts.googleapis.com/css2?family=Work+Sans:wght@400;500;600&display=swap" rel="stylesheet">
<style>
  :root {
    --page-bg: #161616;
    --card-bg: #262626;
    --card-bg-light: #2f2f2f;
    --accent: #f5bf12;
    --text-light: #f2f2f2;
    --text-muted: #8a8a8a;
    --logo-front: #a9a9a9;
  }
  * { box-sizing: border-box; margin: 0; padding: 0; }
  html, body {
    width: 1200px; height: 900px; overflow: hidden;
    background: var(--page-bg);
    font-family: "Work Sans", sans-serif;
  }
  .canvas {
    width: 1200px; height: 900px;
    display: flex; flex-direction: column;
    align-items: center; justify-content: center; gap: 24px;
  }
  .card {
    position: relative;
    width: 700px; height: 400px;
    background: linear-gradient(135deg, var(--card-bg) 0%, var(--card-bg-light) 100%);
    border-bottom: 6px solid var(--accent);
    box-shadow: 0 14px 30px rgba(0,0,0,.55);
    overflow: hidden;
  }
  .brand {
    display: flex; flex-direction: column; align-items: flex-start;
  }
  .brand-row { display: flex; align-items: center; gap: 14px; }
  .brand-mark { width: 22px; height: 22px; border-radius: 50%; }
  .brand-name {
    font-weight: 600; font-size: 34px; letter-spacing: .02em; line-height: 1;
  }
  .brand-tagline {
    margin-top: 8px; margin-left: 36px;
    font-size: 10.5px; letter-spacing: .16em; text-transform: uppercase;
  }

  /* Front */
  .card--front { display: flex; align-items: center; justify-content: center; }
  .card--front .brand-mark { background: var(--logo-front); }
  .card--front .brand-name, .card--front .brand-tagline { color: var(--logo-front); }

  /* Back */
  .card--back .brand {
    position: absolute; left: 56px; top: 168px;
  }
  .card--back .brand-mark { background: var(--text-light); }
  .card--back .brand-name { color: var(--text-light); font-size: 28px; }
  .card--back .brand-tagline { color: var(--text-light); font-size: 8.5px; margin-left: 36px; }
  .divider {
    position: absolute; left: 368px; top: 70px;
    width: 2px; height: 248px; background: var(--accent);
  }
  .contact {
    position: absolute; left: 394px; top: 64px;
    color: var(--text-light);
  }
  .contact-name {
    color: var(--accent); font-weight: 500; font-size: 31px; letter-spacing: .03em; line-height: 1;
  }
  .contact-role { font-size: 17px; margin-top: 4px; letter-spacing: .04em; }
  .contact-list { list-style: none; margin-top: 12px; }
  .contact-list li {
    display: flex; align-items: center; gap: 10px;
    font-size: 18px; letter-spacing: .04em; line-height: 27px;
  }
  .contact-list svg { width: 14px; height: 14px; flex: none; }
  .address { margin-top: 10px; font-size: 18px; letter-spacing: .03em; line-height: 24px; font-style: normal; }
  .address + .address { margin-top: 8px; }
</style>
</head>
<body>
<main class="canvas">
  <section class="card card--front" aria-label="Recto">
    <div class="brand">
      <div class="brand-row">
        <span class="brand-mark"></span>
        <span class="brand-name">Loïc Bardèze</span>
      </div>
      <span class="brand-tagline">Massothérapeute / Préparateur Mental</span>
    </div>
  </section>

  <section class="card card--back" aria-label="Verso">
    <div class="brand">
      <div class="brand-row">
        <span class="brand-mark"></span>
        <span class="brand-name">Loïc Bardèze</span>
      </div>
      <span class="brand-tagline">Massothérapeute / Préparateur Mental</span>
    </div>
    <span class="divider"></span>
    <div class="contact">
      <h1 class="contact-name">LOÏC BARDÈZE</h1>
      <p class="contact-role">Director</p>
      <ul class="contact-list">
        <li>
          <svg viewBox="0 0 24 24" fill="none" stroke="var(--accent)" stroke-width="2.4" stroke-linecap="round" stroke-linejoin="round"><path d="M6 3h4l2 5-3 2a11 11 0 0 0 5 5l2-3 5 2v4a2 2 0 0 1-2 2A17 17 0 0 1 4 5a2 2 0 0 1 2-2z"/></svg>
          078 513 26 48
        </li>
        <li>
          <svg viewBox="0 0 24 24" fill="none" stroke="var(--accent)" stroke-width="2.4" stroke-linejoin="round"><rect x="3" y="5" width="18" height="14" rx="1"/><path d="M3 6l9 7 9-7"/></svg>
          info@loicbardeze.ch
        </li>
        <li>
          <svg viewBox="0 0 24 24" fill="none" stroke="var(--accent)" stroke-width="2"><circle cx="12" cy="12" r="9"/><path d="M3 12h18M12 3c3 3 3 15 0 18M12 3c-3 3-3 15 0 18"/></svg>
          www.loicbardeze.ch
        </li>
      </ul>
      <address class="address">Chemin des Ormilles 7B<br>1400 Yverdon-les-Bains</address>
      <address class="address">Route de la Gravière 9<br>1700 Fribourg</address>
    </div>
  </section>
</main>
</body>
</html>
```